Business Card Design for a Software Startup

We'd like to have a business card design. We already have a logo. Basically what we need is a clean design with name, address, cellphone and phone numbers, e-mail and web site address (front) and a space on the back with our logo with the company name on the right side and some texts on the bottom.
We are a development and consulting company in Brazil with highly qualified team of professionals in Java, iOS and Android development and consulting.

Target Market(s)

CIO, IT managers of mid to big size companies

Industry/Entity Type

Business

```html
<!DOCTYPE html>
<html lang="en">
<head>
<meta charset="utf-8">
<title>BRAXELO business card</title>
<link rel="stylesheet" href="https://fonts.googleapis.com/css2?family=Jost:wght@400;600;700&display=swap">
<style>
  :root {
    --stage: #e6e6ec;
    --card: #ffffff;
    --navy: #0f3c66;
    --blue: #1e6ea6;
    --ink: #2b2b2b;
    --mute: #5a5a5a;
    --faint: #e6f0f6;
    --faint-blue: #b9d9e8;
  }
  * { margin: 0; padding: 0; box-sizing: border-box; }
  html, body { width: 1200px; height: 987px; overflow: hidden; }
  body {
    background: var(--stage);
    font-family: "Jost", "Futura", sans-serif;
    position: relative;
  }
  .card {
    position: absolute;
    left: 220px;
    width: 760px;
    height: 434px;
    background: var(--card);
    border-radius: 30px;
    overflow: hidden;
    box-shadow: 0 6px 18px rgba(0,0,0,0.12);
  }
  .card--front { top: 40px; }
  .card--back { top: 513px; }

  /* front */
  .brand {
    position: absolute;
    left: 42px;
    top: 36px;
    display: flex;
    align-items: center;
    gap: 18px;
  }
  .brand__square {
    width: 74px;
    height: 74px;
    border-radius: 10px;
    background: var(--blue);
  }
  .brand__name {
    font-weight: 700;
    font-size: 104px;
    line-height: 1;
    letter-spacing: 3px;
    color: var(--navy);
  }
  .person {
    position: absolute;
    left: 44px;
    top: 160px;
    font-size: 30px;
    line-height: 1.2;
    color: var(--navy);
    font-weight: 700;
  }
  .person__title { font-weight: 400; color: var(--mute); }
  .contacts {
    position: absolute;
    left: 44px;
    top: 210px;
    list-style: none;
    font-size: 21px;
    color: var(--ink);
    line-height: 31px;
  }
  .contacts li { display: flex; align-items: center; gap: 10px; }
  .contacts svg { width: 16px; height: 16px; fill: var(--navy); }
  .band {
    position: absolute;
    left: 0;
    top: 0;
    width: 760px;
    height: 434px;
  }
  .band__address {
    position: absolute;
    left: 44px;
    top: 381px;
    font-size: 19px;
    line-height: 1.2;
    color: #ffffff;
    white-space: nowrap;
  }

  /* back */
  .back__shape {
    position: absolute;
    left: 250px;
    top: 40px;
    width: 330px;
    height: 330px;
    border-radius: 60px;
    background: var(--faint);
  }
  .back__name {
    position: absolute;
    left: 0;
    right: 0;
    top: 130px;
    text-align: center;
    font-weight: 700;
    font-size: 124px;
    line-height: 1;
    letter-spacing: 5px;
    color: var(--navy);
  }
  .back__web {
    position: absolute;
    left: 0;
    right: 0;
    top: 285px;
    text-align: center;
    font-weight: 600;
    font-size: 22px;
    letter-spacing: 9px;
    color: var(--ink);
  }
</style>
</head>
<body>

<section class="card card--front" aria-label="Business card front">
  <div class="brand">
    <span class="brand__square"></span>
    <span class="brand__name">BRAXELO</span>
  </div>

  <p class="person">Your Name, <span class="person__title">Title</span></p>

  <ul class="contacts">
    <li><svg viewBox="0 0 16 16"><path d="M3 1l3 1 1 3-2 1.5a9 9 0 0 0 4.5 4.5L11 9l3 1 1 3-2 2C7 15 1 9 1 3z"/></svg>123-456-7890</li>
    <li><svg viewBox="0 0 16 16"><rect x="4" y="1" width="8" height="14" rx="1.5"/><rect x="5.5" y="3" width="5" height="7" fill="#fff"/></svg>456-085-4321</li>
    <li><svg viewBox="0 0 16 16"><rect x="1" y="3" width="14" height="10" rx="1.5"/><path d="M1.5 4l6.5 5 6.5-5" stroke="#fff" stroke-width="1.4" fill="none"/></svg>yourname@braxelo.dev</li>
    <li><svg viewBox="0 0 16 16"><circle cx="8" cy="8" r="7"/><path d="M1 8h14M8 1c-3 3.5-3 10.5 0 14M8 1c3 3.5 3 10.5 0 14" stroke="#fff" stroke-width="1" fill="none"/></svg>www.braxelo.dev</li>
  </ul>

  <svg class="band" viewBox="0 0 760 434" aria-hidden="true">
    <rect x="0" y="368" width="760" height="66" fill="var(--navy)"/>
    <rect x="496" y="300" width="210" height="120" rx="18" fill="var(--card)"/>
    <rect x="540" y="286" width="112" height="112" rx="16" fill="var(--faint-blue)"/>
  </svg>
  <p class="band__address">Door No. Street Name City Name, State, Zip Code.</p>
</section>

<section class="card card--back" aria-label="Business card back">
  <div class="back__shape"></div>
  <p class="back__name">BRAXELO</p>
  <p class="back__web">www.braxelo.dev</p>
</section>

</body>
</html>
```